Velmora Freightway Solutions Business cards

Would like a very unique design catchy but professional for business cards. Please use log provided.Marlon WellsCeo and Founder TransCon Logistix Solutions1-888-913-3225mwells@tlsolutionsus.comwww.tlsolutionsus.com

```html
<!DOCTYPE html>
<html lang="en">
<head>
<meta charset="utf-8">
<title>Velmora Freightway Solutions – Business Cards</title>
<link href="https://fonts.googleapis.com/css2?family=Lato:wght@400;700&display=swap" rel="stylesheet">
<style>
  :root {
    --brand-blue: #1473ba;
    --brand-red: #e8212e;
    --ink: #333333;
    --card: #ffffff;
    --backdrop: #e7e4df;
    --rule: #bdbdbd;
  }
  * { box-sizing: border-box; margin: 0; padding: 0; }
  html, body { width: 1200px; height: 960px; overflow: hidden; }
  body {
    background: var(--backdrop);
    font-family: 'Lato', sans-serif;
    position: relative;
  }
  .card {
    position: absolute;
    background: var(--card);
    border-radius: 38px;
    overflow: hidden;
    box-shadow: 0 4px 14px rgba(0,0,0,0.18);
  }
  /* Front */
  .card-front { left: 237px; top: 47px; width: 720px; height: 406px; }
  .front-mark {
    position: absolute; left: 0; right: 0; top: 150px;
    display: flex; align-items: center; justify-content: center; gap: 24px;
  }
  .front-mark .mark-square { width: 78px; height: 78px; background: var(--brand-blue); }
  .front-mark .mark-name {
    color: var(--brand-blue); font-weight: 700; font-size: 44px; line-height: 1.1;
    letter-spacing: 0.5px; text-transform: uppercase;
  }
  .front-web {
    position: absolute; left: 0; right: 0; top: 356px;
    display: flex; align-items: center; justify-content: center; gap: 10px;
  }
  .front-web .web-line { width: 92px; height: 3px; background: var(--brand-blue); border-radius: 2px; }
  .front-web .web-text { font-size: 17px; letter-spacing: 2px; color: var(--ink); }
  /* Back */
  .card-back { left: 245px; top: 507px; width: 705px; height: 408px; }
  .back-mark {
    position: absolute; left: 40px; top: 122px; width: 330px;
    display: flex; align-items: center; gap: 12px;
  }
  .back-mark .mark-square { width: 34px; height: 34px; background: var(--brand-blue); flex: none; }
  .back-mark .mark-name {
    color: var(--brand-blue); font-weight: 700; font-size: 21px; line-height: 1.2;
    letter-spacing: 0.5px; text-transform: uppercase;
  }
  .divider { position: absolute; left: 384px; top: 97px; width: 1px; height: 164px; background: var(--rule); }
  .contact { position: absolute; left: 406px; top: 96px; }
  .person-name { color: var(--brand-blue); font-weight: 700; font-size: 24px; text-transform: uppercase; }
  .person-title { color: var(--brand-red); font-size: 18px; margin-top: 6px; text-transform: uppercase; }
  .contact-list { list-style: none; margin-top: 24px; }
  .contact-list li {
    display: flex; align-items: center; gap: 10px;
    font-size: 17px; color: var(--ink); height: 30px;
  }
  .contact-list svg { width: 15px; height: 15px; flex: none; }
  .address-band {
    position: absolute; left: 0; right: 0; top: 326px; height: 49px;
    border-top: 1px solid var(--ink); border-bottom: 1px solid var(--ink);
  }
  .address-band .band {
    position: absolute; left: 0; right: 0; top: 6px; height: 35px;
    background: var(--brand-blue); color: #fff; font-size: 17px;
    display: flex; align-items: center; padding-left: 180px;
  }
</style>
</head>
<body>
  <section class="card card-front">
    <div class="front-mark">
      <span class="mark-square"></span>
      <span class="mark-name">Velmora Freightway<br>Solutions</span>
    </div>
    <div class="front-web">
      <span class="web-line"></span>
      <span class="web-text">www.vfwayroutes.com</span>
      <span class="web-line"></span>
    </div>
  </section>

  <section class="card card-back">
    <div class="back-mark">
      <span class="mark-square"></span>
      <span class="mark-name">Velmora Freightway Solutions</span>
    </div>
    <div class="divider"></div>
    <div class="contact">
      <p class="person-name">Dorian Pike</p>
      <p class="person-title">CEO and Founder</p>
      <ul class="contact-list">
        <li>
          <svg viewBox="0 0 16 16" aria-hidden="true"><circle cx="8" cy="8" r="7" fill="none" stroke="#1473ba" stroke-width="1.4"/><path d="M5.5 4.5l1.5 0 .6 2-1 .8a5 5 0 0 0 2.2 2.2l.8-1 2 .6v1.5c-3.5.4-6.5-2.6-6.1-6.1z" fill="#1473ba"/></svg>
          1-888-470-6158
        </li>
        <li>
          <svg viewBox="0 0 16 16" aria-hidden="true"><rect x="1" y="3.5" width="14" height="10" rx="1.5" fill="#1473ba"/><path d="M1.5 4.5L8 9l6.5-4.5" fill="none" stroke="#fff" stroke-width="1.3"/></svg>
          dpike@vfwayroutes.com
        </li>
        <li>
          <svg viewBox="0 0 16 16" aria-hidden="true"><g fill="none" stroke="#1473ba" stroke-width="1.2"><circle cx="8" cy="8" r="6.5"/><ellipse cx="8" cy="8" rx="3" ry="6.5"/><path d="M1.5 8h13M2.5 5h11M2.5 11h11"/></g></svg>
          www.vfwayroutes.com
        </li>
      </ul>
    </div>
    <div class="address-band">
      <div class="band">2417 Harlow Creek Rd, Marren, GA 30592</div>
    </div>
  </section>
</body>
</html>
```